Corbell Lending Partners - Real estate loans - need a business card with a logo

I need a logo and a business card that looks elegant - that looks as if it is a big stablish corporation - We do real estate loans, my goal is to brand myself with colors black background - gold or silver letters - some combination - Name of the company different color than the rest of the card -

```html
<!DOCTYPE html>
<html lang="en">
<head>
<meta charset="utf-8">
<title>Corbell Lending Partners – Business Card</title>
<link href="https://fonts.googleapis.com/css2?family=Arimo:wght@400;700&display=swap" rel="stylesheet">
<style>
  :root {
    --stage: #3a3a3c;
    --stage-edge: #1e1e20;
    --navy: #1b2b4f;
    --navy-deep: #15223f;
    --gold: #c6a46a;
    --paper: #ffffff;
    --ink: #4a4a4a;
    --white: #ffffff;
  }
  * { margin: 0; padding: 0; box-sizing: border-box; }
  html, body { width: 1200px; height: 900px; overflow: hidden; }
  body {
    background: radial-gradient(ellipse at 50% 45%, var(--stage) 0%, var(--stage-edge) 100%);
    font-family: "Arimo", Arial, sans-serif;
    position: relative;
  }

  /* Front side: vertical white card */
  .card-front {
    position: absolute;
    left: 150px; top: 160px;
    width: 331px; height: 580px;
    background: var(--paper);
    box-shadow: 0 18px 40px rgba(0,0,0,.45);
    padding: 38px 30px 0 34px;
  }
  .card-front .wordmark {
    font-weight: 700;
    font-size: 21px;
    line-height: 1.1;
    letter-spacing: .04em;
    text-transform: uppercase;
    color: var(--navy);
    text-align: right;
  }
  .card-front .accent-bar {
    position: absolute;
    left: 0; top: 118px;
    width: 10px; height: 26px;
    background: var(--navy);
  }
  .contact { margin-top: 32px; }
  .contact .person-name {
    font-size: 20px;
    font-weight: 400;
    letter-spacing: .03em;
    text-transform: uppercase;
    color: var(--gold);
  }
  .contact .person-role {
    font-size: 13px;
    color: var(--ink);
    margin-top: 4px;
  }
  .contact .address {
    font-size: 13px;
    line-height: 1.4;
    color: var(--ink);
    margin-top: 12px;
  }
  .contact ul { list-style: none; margin-top: 10px; }
  .contact li {
    font-size: 13px;
    line-height: 1.5;
    color: var(--ink);
    display: flex;
    align-items: center;
    gap: 7px;
  }
  .contact li svg { width: 10px; height: 10px; flex: none; }
  .front-emblem {
    position: absolute;
    left: 86px; top: 350px;
    width: 160px; height: 160px;
    border: 8px solid var(--gold);
    background: var(--paper);
    display: flex; align-items: center; justify-content: center;
  }
  .front-emblem span {
    width: 104px; height: 104px;
    background: var(--navy);
  }

  /* Back side: horizontal navy card */
  .card-back {
    position: absolute;
    left: 560px; top: 290px;
    width: 580px; height: 331px;
    background: linear-gradient(160deg, var(--navy) 0%, var(--navy-deep) 100%);
    box-shadow: 0 18px 40px rgba(0,0,0,.5);
    display: flex; flex-direction: column; align-items: center; justify-content: center;
  }
  .card-back .brand-lockup {
    display: flex; align-items: center; gap: 14px;
  }
  .card-back .brand-square {
    width: 18px; height: 18px;
    background: var(--gold);
  }
  .card-back .wordmark {
    font-weight: 700;
    font-size: 24px;
    letter-spacing: .05em;
    text-transform: uppercase;
    color: var(--white);
  }
  .card-back .web-line {
    margin-top: 28px;
    display: flex; align-items: center; gap: 14px;
    font-size: 14px;
    color: var(--white);
    letter-spacing: .02em;
  }
  .card-back .web-line i {
    display: block; width: 130px; height: 1px;
    background: linear-gradient(90deg, transparent, rgba(255,255,255,.8));
  }
  .card-back .web-line i.right {
    background: linear-gradient(90deg, rgba(255,255,255,.8), transparent);
  }
</style>
</head>
<body>

  <section class="card-front" aria-label="Card front">
    <h1 class="wordmark">Corbell<br>Lending Partners</h1>
    <div class="accent-bar"></div>
    <div class="contact">
      <p class="person-name">Daniel Hart</p>
      <p class="person-role">Founder</p>
      <p class="address">418 Birchwood Lane<br>Ashford, WA 98304</p>
      <ul>
        <li>
          <svg viewBox="0 0 10 10"><path d="M2 1l2 2-1 1.2a6 6 0 0 0 2.8 2.8L7 6l2 2-1.2 1.3C4.5 9 1 5.5.7 2.2z" fill="var(--gold)"/></svg>
          555 210 4837
        </li>
        <li>
          <svg viewBox="0 0 10 10"><rect x=".5" y="2" width="9" height="6" fill="none" stroke="var(--gold)"/><path d="M.5 2l4.5 3.5L9.5 2" fill="none" stroke="var(--gold)"/></svg>
          info@corbelllending.com
        </li>
        <li>
          <svg viewBox="0 0 10 10"><circle cx="5" cy="5" r="4.3" fill="var(--gold)"/></svg>
          www.corbelllending.com
        </li>
      </ul>
    </div>
    <div class="front-emblem" aria-hidden="true"><span></span></div>
  </section>

  <section class="card-back" aria-label="Card back">
    <div class="brand-lockup">
      <span class="brand-square"></span>
      <h2 class="wordmark">Corbell Lending Partners</h2>
    </div>
    <p class="web-line"><i></i>www.corbelllending.com<i class="right"></i></p>
  </section>

</body>
</html>
```